BLS Business Card 2018

Larkmere Chiropractic. We have two locations that we want to advertise on the same card. Brightvale OrthoCore campus address: 3815 Pellham Dr., Suite 240, Flowood, MS 39417. Madison address: 246 Willowmere Dr., Building D., Madison, MS 39284. website: www.drlarkmere-example.com. o:(601)555-0147 f:(601)555-0183

Target Market(s)

Health care decision makers: primary care doctors and mothers

Contact Information for Business Card

I have no idea; up for any suggestions and I'd do much better picking from examples versus describing what I'm looking for. We are in a very high end location and would like the cards to look really sharp.

Requirements
Must have
• My name, Martin R Belvane, D.C.

```html
<!DOCTYPE html>
<html lang="en">
<head>
<meta charset="utf-8">
<title>Larkmere Chiropractic – Business Card</title>
<link rel="stylesheet" href="https://fonts.googleapis.com/css2?family=Cinzel:wght@600&family=Merriweather:wght@400;700&display=swap">
<style>
  :root {
    --backdrop: #dcdcdc;
    --card-blue: #0d5a7b;
    --accent-teal: #3fb3c6;
    --paper: #f7f7f7;
    --text-light: #ffffff;
    --text-soft: #d5e6ee;
    --brand-blue: #0d5a7b;
  }
  * { box-sizing: border-box; margin: 0; padding: 0; }
  html, body { width: 1200px; height: 852px; overflow: hidden; background: var(--backdrop); }
  .canvas { position: relative; width: 1200px; height: 852px; background: var(--backdrop); }

  .card {
    position: absolute; top: 283px; width: 500px; height: 286px;
    border-radius: 22px; overflow: hidden; background: var(--card-blue);
    box-shadow: 0 6px 14px rgba(0,0,0,.25);
  }
  .card--front { left: 70px; }
  .card--back { left: 630px; }

  .brand {
    font-family: "Cinzel", Georgia, serif; font-weight: 600;
    line-height: 1; letter-spacing: .5px; text-transform: uppercase;
    white-space: nowrap;
  }

  /* Front */
  .front-figure {
    position: absolute; left: 40px; top: 20px; width: 200px; height: 266px;
    border-radius: 40% 40% 0 0;
    background: radial-gradient(ellipse at 50% 45%, rgba(63,179,198,.35), rgba(63,179,198,0) 70%);
  }
  .front-brand {
    position: absolute; left: 250px; top: 100px; color: var(--text-light);
  }
  .front-brand span { display: block; font-size: 34px; }
  .front-brand span + span { font-size: 27px; margin-top: 2px; }

  /* Back */
  .back-shape { position: absolute; inset: 0; }
  .back-figure {
    position: absolute; left: 388px; top: 34px; width: 62px; height: 78px;
    border-radius: 40% 40% 10% 10%;
    background: radial-gradient(ellipse at 50% 45%, rgba(40,40,40,.22), rgba(40,40,40,0) 72%);
  }
  .back-brand {
    position: absolute; right: 24px; top: 120px; color: var(--brand-blue); text-align: right;
  }
  .back-brand span { display: block; font-size: 22px; }
  .back-brand span + span { font-size: 18px; margin-top: 2px; }

  .holder { position: absolute; left: 28px; top: 50px; color: var(--text-light); font-family: "Merriweather", Georgia, serif; }
  .holder-name { font-size: 15px; font-weight: 700; }
  .holder-title { font-size: 8px; color: var(--text-soft); margin-top: 4px; }

  .contact {
    position: absolute; left: 28px; top: 150px; list-style: none;
    font-family: "Merriweather", Georgia, serif; font-size: 9.5px; color: var(--text-light);
  }
  .contact li { display: flex; align-items: flex-start; line-height: 13px; }
  .contact svg { width: 10px; height: 10px; flex: none; margin: 1px 10px 0 0; fill: var(--text-light); }
</style>
</head>
<body>
<main class="canvas">

  <section class="card card--front">
    <div class="front-figure" role="img" aria-label="Line drawing of a human back and torso in teal"></div>
    <div class="front-brand brand"><span>Larkmere</span><span>Chiropractic</span></div>
  </section>

  <section class="card card--back">
    <svg class="back-shape" viewBox="0 0 500 286" width="500" height="286">
      <path d="M230 0 Q250 210 500 240 L500 0 Z" fill="var(--paper)"/>
      <path d="M230 0 Q250 210 500 240" fill="none" stroke="var(--accent-teal)" stroke-width="7"/>
    </svg>
    <div class="back-figure" role="img" aria-label="Small line drawing of a human torso"></div>
    <div class="back-brand brand"><span>Larkmere</span><span>Chiropractic</span></div>

    <div class="holder">
      <p class="holder-name">Martin R Belvane, D.C.</p>
      <p class="holder-title">Managing Director</p>
    </div>

    <ul class="contact">
      <li><svg viewBox="0 0 10 10"><path d="M2 0.5 L3.8 2.8 L2.8 3.8 Q4 6 6.2 7.2 L7.2 6.2 L9.5 8 L8.2 9.5 Q2 9 0.5 1.8 Z"/></svg>(601)555-0147</li>
      <li><svg viewBox="0 0 10 10"><rect x="2.5" y="0.5" width="5" height="3"/><rect x="0.5" y="3.5" width="9" height="4.5" rx="1"/><rect x="2.5" y="7" width="5" height="2.5"/></svg>(601)555-0183</li>
      <li><svg viewBox="0 0 10 10"><path d="M0.5 2 H9.5 V8.5 H0.5 Z M0.5 2 L5 5.5 L9.5 2" fill="none" stroke="#fff" stroke-width="1.2"/></svg>m.r.belvane@drlarkmere-example.com</li>
      <li><svg viewBox="0 0 10 10"><circle cx="5" cy="5" r="4.3" fill="none" stroke="#fff" stroke-width="1.1"/><path d="M0.7 5 H9.3 M5 0.7 Q2 5 5 9.3 M5 0.7 Q8 5 5 9.3" fill="none" stroke="#fff" stroke-width=".9"/></svg>www.drlarkmere-example.com</li>
      <li><svg viewBox="0 0 10 10"><path d="M5 0.5 A3.3 3.3 0 0 1 8.3 3.8 Q8.3 6 5 9.5 Q1.7 6 1.7 3.8 A3.3 3.3 0 0 1 5 0.5 Z M5 2.6 A1.2 1.2 0 1 0 5 5 A1.2 1.2 0 1 0 5 2.6 Z" fill-rule="evenodd"/></svg><span>3815 Pellham Dr., Suite 240,<br>Flowood, MS 39417</span></li>
      <li><svg viewBox="0 0 10 10"><path d="M5 0.5 A3.3 3.3 0 0 1 8.3 3.8 Q8.3 6 5 9.5 Q1.7 6 1.7 3.8 A3.3 3.3 0 0 1 5 0.5 Z M5 2.6 A1.2 1.2 0 1 0 5 5 A1.2 1.2 0 1 0 5 2.6 Z" fill-rule="evenodd"/></svg><span>246 Willowmere Dr., Building D.,<br>Madison, MS 39284</span></li>
    </ul>
  </section>

</main>
</body>
</html>
```